Business card for event manager / organizer "waiter service"

Draft of a new valuable business card for my company.
Events, personnel service providers, festivals

```html
<!DOCTYPE html>
<html lang="de">
<head>
<meta charset="utf-8">
<title>Servierwerk Eventpersonal – Visitenkarte</title>
<link href="https://fonts.googleapis.com/css2?family=Open+Sans:wght@400;600;800&display=swap" rel="stylesheet">
<style>
  :root {
    --stage: #e9e6e1;
    --card-dark: #1f1d23;
    --orange: #e07a1f;
    --orange-deep: #7a3a0c;
    --white: #ffffff;
    --muted: #cfcfd4;
  }
  * { box-sizing: border-box; margin: 0; padding: 0; }
  html, body { width: 1200px; height: 900px; overflow: hidden; }
  body {
    background: var(--stage);
    font-family: "Open Sans", Arial, sans-serif;
    position: relative;
  }
  .card {
    position: absolute;
    width: 560px;
    height: 364px;
    background: var(--card-dark);
    overflow: hidden;
    box-shadow: 0 8px 24px rgba(0,0,0,.25);
  }
  .card--front { left: 110px; top: 64px; }
  .card--back  { left: 530px; top: 472px; }

  /* brand block */
  .brand { position: absolute; color: var(--white); }
  .brand__row { display: flex; align-items: center; gap: 10px; }
  .brand__mark { width: 16px; height: 16px; background: var(--orange); flex: none; }
  .brand__name {
    font-weight: 800; font-size: 26px; letter-spacing: .5px;
    line-height: 1.05; text-transform: uppercase; white-space: nowrap;
  }
  .brand__sub {
    display: block; font-size: 13px; font-weight: 600; letter-spacing: 1px;
    text-transform: uppercase; color: var(--white); line-height: 1.2;
  }
  .brand__tagline {
    display: block; font-size: 10px; font-weight: 400;
    color: var(--muted); margin-top: 5px; padding-left: 26px; white-space: nowrap;
  }

  /* front */
  .card--front .brand { left: 160px; top: 28px; }
  .front__rule {
    position: absolute; left: 100px; width: 360px; height: 2px; background: var(--orange);
  }
  .front__rule--top { top: 104px; }
  .front__rule--bottom { top: 150px; }
  .front__social {
    position: absolute; left: 0; right: 0; top: 113px;
    text-align: center; color: var(--white); font-size: 19px; font-weight: 400;
  }
  .front__social-dot {
    display: inline-block; width: 15px; height: 15px; border-radius: 50%;
    background: var(--white); margin-right: 8px; vertical-align: -1px;
  }
  .front__photo {
    position: absolute; left: 0; right: 0; bottom: 0; height: 200px;
    background: linear-gradient(90deg, #3a3f3a 0%, #8c9a6a 30%, #5f8f3a 48%, #6a6f86 65%, #d98a78 85%, #2a2740 100%);
    opacity: .85;
  }

  /* back */
  .back__wave { position: absolute; inset: 0; }
  .card--back .brand { left: 272px; top: 44px; }
  .back__portrait {
    position: absolute; left: 36px; top: 58px; width: 168px; height: 170px;
    border: 3px solid var(--orange); border-radius: 20px;
    background: radial-gradient(circle at 50% 40%, #8a8a8a, #3a3a3a 70%, #222 100%);
  }
  .back__person { position: absolute; left: 36px; top: 236px; color: var(--white); }
  .back__name { font-size: 22px; font-weight: 800; line-height: 1.1; }
  .back__role { font-size: 15px; font-weight: 400; margin-bottom: 6px; }
  .contact-list { list-style: none; }
  .contact-list li {
    font-size: 13px; line-height: 1.45; display: flex; align-items: center; gap: 8px;
  }
  .contact-list--right { position: absolute; right: 22px; top: 256px; color: var(--white); }
  .contact-list--right li { justify-content: flex-end; }
  .icon { width: 12px; height: 12px; fill: var(--card-dark); flex: none; }
</style>
</head>
<body>

<section class="card card--front" aria-label="Visitenkarte Vorderseite">
  <div class="brand">
    <div class="brand__row">
      <span class="brand__mark"></span>
      <span class="brand__name">Servierwerk<span class="brand__sub">Eventpersonal</span></span>
    </div>
    <span class="brand__tagline">…Ihr Team für Feste und Events</span>
  </div>
  <div class="front__rule front__rule--top"></div>
  <p class="front__social"><span class="front__social-dot"></span>/servierwerkEvents</p>
  <div class="front__rule front__rule--bottom"></div>
  <div class="front__photo" role="img" aria-label="Foto: Reihe bunter Gin-Tonic-Cocktails in Stielgläsern mit Früchten und Kräutern"></div>
</section>

<section class="card card--back" aria-label="Visitenkarte Rückseite">
  <svg class="back__wave" viewBox="0 0 560 364" preserveAspectRatio="none" aria-hidden="true">
    <defs>
      <linearGradient id="metal" x1="0" y1="0" x2="1" y2="0">
        <stop offset="0" stop-color="#7a3a0c"/>
        <stop offset=".3" stop-color="#e07a1f"/>
        <stop offset=".5" stop-color="#8a420f"/>
        <stop offset=".75" stop-color="#f08a2a"/>
        <stop offset="1" stop-color="#a04e12"/>
      </linearGradient>
    </defs>
    <path d="M0 264 C120 214 230 226 330 196 C430 166 500 120 560 70 L560 364 L0 364 Z" fill="url(#metal)"/>
    <path d="M300 200 C410 170 490 120 560 58 L560 70 C500 120 430 166 330 196 Z" fill="#1f1d23"/>
    <path d="M360 190 C450 160 510 115 560 40 L560 52 C515 120 460 165 380 186 Z" fill="#e07a1f"/>
  </svg>

  <div class="brand">
    <div class="brand__row">
      <span class="brand__mark"></span>
      <span class="brand__name">Servierwerk<span class="brand__sub">Eventpersonal</span></span>
    </div>
    <span class="brand__tagline">…Ihr Team für Feste und Events</span>
  </div>

  <div class="back__portrait" role="img" aria-label="Porträtfoto des Inhabers in Weste und weißem Hemd"></div>

  <div class="back__person">
    <p class="back__name">Fenno Hartwig</p>
    <p class="back__role">Inhaber</p>
    <ul class="contact-list">
      <li><svg class="icon" viewBox="0 0 12 12"><rect x="3" y="0.5" width="6" height="11" rx="1"/></svg>0151 234 56 78</li>
      <li><svg class="icon" viewBox="0 0 12 12"><path d="M1 4 Q6 0 11 4 L9 6 L8 4.5 Q6 4 4 4.5 L3 6 Z M2 11 L3 6 H9 L10 11 Z"/></svg>02361 555 01 23</li>
      <li><svg class="icon" viewBox="0 0 12 12"><path d="M1 3 H11 V10 H1 Z"/></svg>info@servierwerk-events.de</li>
    </ul>
  </div>

  <ul class="contact-list contact-list--right">
    <li>Lindenweg 12, 45000 Musterstadt<svg class="icon" viewBox="0 0 12 12"><path d="M6 0.5 A4 4 0 0 1 10 4.5 C10 7 6 11.5 6 11.5 C6 11.5 2 7 2 4.5 A4 4 0 0 1 6 0.5 Z"/></svg></li>
    <li>www.servierwerk-events.de<svg class="icon" viewBox="0 0 12 12"><circle cx="6" cy="6" r="5"/></svg></li>
  </ul>
</section>

</body>
</html>
```